Moravel Aesthetic Doctor

I require an elegant, luxurious looking business card for my aesthetic business. I am a doctor and that will set me aside from competitors. I am planning to provide home and spa based treatments to clients with high expectations. I have attached my logo.

```html
<!DOCTYPE html>
<html lang="en">
<head>
<meta charset="utf-8">
<title>Moravel Aesthetic Doctor – Business Card</title>
<link href="https://fonts.googleapis.com/css2?family=Open+Sans:wght@400;600&display=swap" rel="stylesheet">
<style>
  :root {
    --page-bg: #e4e4e4;
    --brand-blue: #1a78bb;
    --accent-blue: #1f9ad6;
    --soft-grey: #a7a9ac;
    --card-white: #f4f4f4;
    --ink: #333333;
    --white: #ffffff;
    --band-1: #1a6fb0;
    --band-2: #1e7fc0;
    --band-3: #2b90cf;
    --band-4: #4aa6db;
    --band-5: #74bde6;
    --band-6: #a3d4ef;
  }
  * { margin: 0; padding: 0; box-sizing: border-box; }
  html, body { width: 1200px; height: 960px; overflow: hidden; }
  body {
    background: var(--page-bg);
    font-family: "Open Sans", Arial, sans-serif;
    position: relative;
  }
  .card {
    position: absolute;
    left: 320px;
    width: 560px;
    height: 342px;
  }
  /* Front */
  .card-front { top: 119px; background: var(--brand-blue); }
  .front-brand {
    position: absolute;
    left: 0; right: 0; top: 200px;
  }
  .front-logo {
    position: absolute;
    top: 92px; left: 0; right: 0;
    display: flex; align-items: center; justify-content: center;
    gap: 22px;
  }
  .brand-circle {
    width: 86px; height: 86px;
    border: 3px solid var(--soft-grey);
    border-radius: 50%;
    flex: none;
  }
  .brand-name {
    color: var(--soft-grey);
    font-weight: 400;
    line-height: 1.05;
  }
  .brand-name .brand-main { display: block; font-size: 50px; letter-spacing: 2px; }
  .brand-name .brand-sub { display: block; font-size: 23px; letter-spacing: 1.5px; }
  .services {
    position: absolute;
    top: 250px; left: 0; right: 0;
    text-align: center;
    color: var(--white);
    font-size: 17px;
    line-height: 21px;
  }
  /* Back */
  .card-back { top: 498px; background: var(--card-white); }
  .side-band {
    position: absolute; left: 0; top: 0;
    width: 15px; height: 100%;
    display: flex; flex-direction: column;
  }
  .side-band span { flex: 1; }
  .side-band span:nth-child(1) { background: var(--band-1); }
  .side-band span:nth-child(2) { background: var(--band-2); }
  .side-band span:nth-child(3) { background: var(--band-3); }
  .side-band span:nth-child(4) { background: var(--band-4); }
  .side-band span:nth-child(5) { background: var(--band-5); }
  .side-band span:nth-child(6) { background: var(--band-6); }
  .back-mark {
    position: absolute;
    top: 34px; right: 32px;
    display: flex; align-items: center; gap: 12px;
  }
  .back-mark .brand-circle { width: 70px; height: 70px; }
  .back-mark .brand-name { color: var(--accent-blue); font-size: 26px; letter-spacing: 2px; }
  .holder {
    position: absolute; left: 49px; top: 167px;
  }
  .holder-name { font-size: 19px; color: var(--ink); line-height: 24px; }
  .holder-name .post-nominals { font-size: 12px; color: var(--accent-blue); margin-left: 2px; }
  .holder-title { font-size: 14px; color: var(--accent-blue); line-height: 19px; }
  .divider {
    position: absolute; left: 49px; top: 225px;
    width: 470px; height: 1.5px;
    background: var(--accent-blue);
  }
  .contacts {
    position: absolute; left: 48px; top: 241px;
    list-style: none;
    color: var(--ink); font-size: 16px; line-height: 21.5px;
  }
  .contacts li { display: flex; align-items: center; gap: 4px; }
  .contacts svg { width: 14px; height: 14px; flex: none; }
  .social {
    position: absolute; right: 40px; top: 287px;
    display: flex; gap: 4px;
  }
  .social span {
    width: 13px; height: 13px; border-radius: 50%;
    background: var(--accent-blue);
  }
</style>
</head>
<body>
  <section class="card card-front" aria-label="Card front">
    <div class="front-logo">
      <div class="brand-circle"></div>
      <div class="brand-name">
        <span class="brand-main">MORAVEL</span>
        <span class="brand-sub">AESTHETIC DOCTOR</span>
      </div>
    </div>
    <p class="services">
      Dermal injectables - Plasma facials - Microneedling<br>
      Skin boosters - Excessive sweating<br>
      Home and Spa Based Treatments
    </p>
  </section>

  <section class="card card-back" aria-label="Card back">
    <div class="side-band"><span></span><span></span><span></span><span></span><span></span><span></span></div>
    <div class="back-mark">
      <div class="brand-name">MORAVEL</div>
      <div class="brand-circle"></div>
    </div>
    <div class="holder">
      <p class="holder-name">Dr Elsa Varno <span class="post-nominals">MRCPCH MD</span></p>
      <p class="holder-title">Australasian Diploma of Aesthetic Medicine</p>
    </div>
    <div class="divider"></div>
    <ul class="contacts">
      <li>
        <svg viewBox="0 0 16 16" aria-hidden="true"><path fill="#1f9ad6" d="M3.6 1.2l2.3 2.6-1.3 2c.9 2 2.4 3.5 4.4 4.4l2-1.3 2.6 2.3-1 2.3C7 13.6 2.4 9 1.2 4.3z"/></svg>
        0800 555 014
      </li>
      <li>
        <svg viewBox="0 0 16 16" aria-hidden="true"><rect x="1.5" y="3.5" width="13" height="9" fill="none" stroke="#1f9ad6" stroke-width="1.5"/><path d="M1.5 3.5L8 9l6.5-5.5" fill="none" stroke="#1f9ad6" stroke-width="1.5"/></svg>
        elsa@moravel.co.nz
      </li>
      <li>
        <svg viewBox="0 0 16 16" aria-hidden="true"><g fill="none" stroke="#1f9ad6" stroke-width="1.2"><circle cx="8" cy="8" r="6.3"/><ellipse cx="8" cy="8" rx="2.8" ry="6.3"/><path d="M1.7 8h12.6M2.8 4.8h10.4M2.8 11.2h10.4"/></g></svg>
        www.moravel.co.nz
      </li>
    </ul>
    <div class="social"><span></span><span></span></div>
  </section>
</body>
</html>
```